tallow-brook.com

We are a small dollar lending company that will revolutionize the industry. We will do this by being completely transparent, fee free, etc and an interest rate that normal people can afford to pay. Over 10X less than our competition. We only allow our members to pay bills " bills paid fast", within 72 hours. Payday loans typically charge from 390%-600% with a terrible payback structure. We charge 36%, period, with a payback structure over 12 months. Our site will be very simple and easy to use but elegant at the same time. We do not want the site to be too busy, less is more and easier. We will have; Home, The Story, Why tallowbrook.com, Are you eligible? Members, Clients. To become a member you have to be referred by a current client of tallowbrook.com. A lot of the busy stuff will be saved for the Members and Clients sections. The feel must be elegant, easy to use and very simple to understand. I am looking for the green, white and black combinations of colors, very similar to my logo that was designed by Fernquillo.

```html
<!DOCTYPE html>
<html lang="en">
<head>
<meta charset="utf-8">
<title>tallow-brook.com</title>
<link rel="stylesheet" href="https://fonts.googleapis.com/css2?family=Arimo:wght@400&display=swap">
<style>
  :root {
    --brand-green: #8dc63f;
    --ink: #1a1a1a;
    --paper: #ffffff;
  }
  * { margin: 0; padding: 0; box-sizing: border-box; }
  html, body {
    width: 1200px;
    height: 876px;
    overflow: hidden;
    background: var(--paper);
  }
  .page {
    position: relative;
    width: 1200px;
    height: 876px;
    overflow: hidden;
    font-family: "Arimo", Arial, sans-serif;
    background: var(--paper);
  }
  .green-field {
    position: absolute;
    inset: 0;
    width: 1200px;
    height: 876px;
  }
  .brand {
    position: absolute;
    left: 43px;
    top: 40px;
    display: flex;
    align-items: center;
    gap: 10px;
    font-size: 19px;
    color: var(--ink);
    letter-spacing: 0.2px;
  }
  .brand-dot {
    width: 30px;
    height: 30px;
    border-radius: 50%;
    background: var(--brand-green);
  }
  .main-nav {
    position: absolute;
    left: 41px;
    top: 241px;
    list-style: none;
  }
  .main-nav li {
    height: 65px;
    font-size: 19px;
    line-height: 24px;
    color: var(--ink);
    text-transform: uppercase;
  }
  .main-nav li.is-active { color: var(--brand-green); }
  .promise-list {
    position: absolute;
    left: 871px;
    top: 359px;
    list-style: none;
  }
  .promise-list li {
    height: 38.4px;
    font-size: 16.5px;
    line-height: 22px;
    color: var(--paper);
    text-transform: uppercase;
  }
  .copyright {
    position: absolute;
    left: 535px;
    top: 845px;
    font-size: 12.5px;
    color: var(--paper);
    white-space: pre;
  }
  .copyright-label { color: var(--brand-green); }
</style>
</head>
<body>
<div class="page">
  <svg class="green-field" viewBox="0 0 1200 876" aria-hidden="true">
    <polygon points="564,0 1200,0 1200,876 600,876 600,312" fill="var(--brand-green)"/>
  </svg>

  <div class="brand">
    <span class="brand-dot"></span>
    <span class="brand-name">tallow-brook.com</span>
  </div>

  <ul class="main-nav">
    <li>Home</li>
    <li>The Story</li>
    <li>Why tallowbrook.com</li>
    <li class="is-active">Are you eligible ?</li>
    <li>Members</li>
    <li>Clients</li>
  </ul>

  <ul class="promise-list">
    <li>36 %, not 390 - 600 %</li>
    <li>Transparent</li>
    <li>Fee free</li>
    <li>Bill paid within 72 hrs</li>
    <li>Payback structure over 12 months</li>
  </ul>

  <p class="copyright"><span class="copyright-label">Copyright : </span>TALLOW-BROOK.COM    2014</p>
</div>
</body>
</html>
```